Velmori Sciences needs high end Label Design for a revolutionary new supplement

We at Velmori Sciences are looking for a brand new Label Design for a first of its kind product called Solvenna. It is the first supplement on the market that treats grief and heartbreak. This product is unisex for both men and woman. We want the New Label to look high end and luxurious using the brand colors which are gold and burgundy. Please feel free to use other colors such as black, white, or gray to go along with it or any other colors if you feel would be a great fit! Velmori Sciences is like the Tarnwick of the supplement world, coming out with new products that will challenge the way people treat different symptoms. To Recap:

1. Product Name: SOLVENNA - the font will play a big roll
2. The Label will be placed on an all white bottle
3. Some parts of the label will be printed with foil to make parts of the label shiny and more attractive. Please keep this in mind when designing.
4. Must use our Logo. I will attach a file of our logo and of the emblem as well. Feel free to use the emblem separately if you have a great idea for it. Please let us know if you need the Logo in a different file type.
5. This all natural herbal supplement in pill form is the first to treat grief and support someone with a broken heart. The consumers purchasing this product will be going through a hard and emotional time. This is a serious product.
6. The manufacturer has included some basic instructions regarding the dye line and file types. Please do your best to meet these. If you cannot meet the guidelines please submit art work anyways. If your design is chosen we will just have the manufacturer replicate the design.

The final label should portray Solvenna and Velmori Sciences as a luxurious brand and product which was made with cutting edge science leading the way with revolutionary ideas. We want customers to feel that the product is worth every penny, because it is. As soon as they receive the product and take one look at the label, I want them to think WOW I made the right choice buying this. I have attached some Label designs that we really liked for your review.

Please feel free to message me with any questions or if you need the Logo in a different file type. Thank you all.
Updates

Please send in more entries while we take a couple days to review, we are still looking for that one design we can work with. We are getting close, thank you all!

Target Market(s)

People going through grief and heartbreak.

Font styles to use
Sans Serif
Script
Other font styles liked:
• Any font that looks good, The font for the name SOLVENNA is very important and will brand it. We hated the font used in the label we received in our first label draft (attached so you can see)

Requirements
Must have
• Must have the company Logo that says the company name
• Must have the colors Gold and Burgundy
• Must have some areas that will be the shiny foil when label is printed.
• Must say "Dietary Supplement" somewhere near the bottom along with "90 Capsules"
• I have attached a Label someone designed for us but were not really happy with. I did like the font the "Dietary supplement" and "90 Capsules" had and also where it was placed. We absolutely HATED the font used for Solvenna.
• Must look at the label design we received from the manufacturer and take into consideration the room needed to write in the directions and all the symbols such as "made in america" and "KMT Facility" Don't worry about adding these in as they will put those in before printing but keep in mind they will be added to the Final Label along with the Supplement Facts.
Nice to have
• Would like to see other colors to go with gold and burgundy suck as black, white, or gray. I have attached some Label designs that I really liked for your reference.
Should not have
• Does not need to have any other legal language, that will be applied by the the manufacturer's graphics team.

```html
<!DOCTYPE html>
<html lang="en">
<head>
<meta charset="utf-8">
<title>Solvenna Label – Velmori Sciences</title>
<link href="https://fonts.googleapis.com/css2?family=Cinzel:wght@500&family=Raleway:wght@200;500;700&display=swap" rel="stylesheet">
<style>
  :root {
    --backdrop: #ededee;
    --label-black: #0b0b0c;
    --mandala-tone: #2a2426;
    --text-white: #f4f4f4;
    --gold: #c9a45c;
    --gold-light: #ecd596;
    --burgundy-deep: #3a0c18;
    --burgundy: #6a1a2c;
  }
  html, body {
    margin: 0;
    padding: 0;
    width: 1200px;
    height: 1200px;
    overflow: hidden;
    background: var(--backdrop);
  }
  .canvas {
    position: relative;
    width: 1200px;
    height: 1200px;
  }
  .label {
    position: absolute;
    left: 100px;
    top: 100px;
    width: 1000px;
    height: 1000px;
    background: var(--label-black);
    overflow: hidden;
  }
  .ornament-field {
    position: absolute;
    left: 40px;
    top: 110px;
    width: 920px;
    height: 920px;
  }
  .brand {
    position: absolute;
    left: 0;
    top: 90px;
    width: 100%;
    text-align: center;
    color: var(--gold);
  }
  .brand-mark {
    display: block;
    width: 80px;
    height: 80px;
    margin: 0 auto 22px;
    border-radius: 50%;
    background: var(--gold);
  }
  .brand-name {
    font-family: "Cinzel", serif;
    font-weight: 500;
    font-size: 40px;
    letter-spacing: 3px;
    line-height: 1;
    margin: 0;
  }
  .brand-name span {
    display: block;
    font-size: 28px;
    letter-spacing: 5px;
    margin-top: 4px;
  }
  .emblem-diamond {
    position: absolute;
    left: 260px;
    top: 330px;
    width: 490px;
    height: 490px;
  }
  .product-name {
    position: absolute;
    left: 0;
    top: 510px;
    width: 100%;
    text-align: center;
    font-family: "Raleway", sans-serif;
    font-weight: 200;
    font-size: 122px;
    letter-spacing: 6px;
    line-height: 1;
    color: var(--text-white);
    margin: 0;
    padding-left: 16px;
    box-sizing: border-box;
  }
  .product-info {
    position: absolute;
    left: 612px;
    top: 752px;
    color: var(--gold);
    font-family: "Raleway", sans-serif;
  }
  .product-type {
    font-weight: 500;
    font-size: 21px;
    letter-spacing: 1px;
    line-height: 1.1;
    margin: 0;
  }
  .capsule-count {
    margin: 6px 0 0;
    font-weight: 700;
    font-size: 42px;
    line-height: 1;
  }
  .capsule-count span {
    font-weight: 500;
    font-size: 12px;
    letter-spacing: 1px;
    vertical-align: middle;
  }
</style>
</head>
<body>
<div class="canvas">
  <section class="label">
    <svg class="ornament-field" viewBox="0 0 920 920" role="img" aria-label="Circular botanical mandala ornament in fine line work around the center of the label">
      <defs>
        <radialGradient id="mandala-tone" cx="50%" cy="50%" r="50%">
          <stop offset="0%" stop-color="#2a2426"/>
          <stop offset="60%" stop-color="#1a1516"/>
          <stop offset="100%" stop-color="#0b0b0c"/>
        </radialGradient>
      </defs>
      <circle cx="460" cy="460" r="460" fill="url(#mandala-tone)"/>
    </svg>

    <header class="brand">
      <span class="brand-mark"></span>
      <p class="brand-name">VELMORI<span>SCIENCES</span></p>
    </header>

    <svg class="emblem-diamond" viewBox="0 0 490 490" aria-hidden="true">
      <defs>
        <linearGradient id="diamond-fill" x1="0" y1="0" x2="1" y2="1">
          <stop offset="0%" stop-color="#6a1a2c"/>
          <stop offset="100%" stop-color="#3a0c18"/>
        </linearGradient>
        <linearGradient id="diamond-edge" x1="0" y1="0" x2="1" y2="1">
          <stop offset="0%" stop-color="#ecd596"/>
          <stop offset="50%" stop-color="#c9a45c"/>
          <stop offset="100%" stop-color="#ecd596"/>
        </linearGradient>
      </defs>
      <polygon points="245,4 486,245 245,486 4,245" fill="url(#diamond-fill)" stroke="url(#diamond-edge)" stroke-width="3"/>
    </svg>

    <h1 class="product-name">SOLVENNA</h1>

    <div class="product-info">
      <p class="product-type">DIETARY<br>SUPPLEMENT</p>
      <p class="capsule-count">90 <span>CAPSULES</span></p>
    </div>
  </section>
</div>
</body>
</html>
```